physio rehab flyer for Vela Mend please

Specification:
Flyer is to be trifold from letter size (8.5 x 11)
-----------------------This may help you:--------------------------
I would like the look of :
clean, minimalistic look with mainly blue and green
san serif font
professional
The colors I like are blue (not the blue in the logo enclosed, I want a change, but more like the blue on my website logo) and light green.
This is my website: www.velamendgroup.ca just so you get an idea but it will be totally changed soon to a to be determined design.
I like the blue and green in file "sample 2" (enclosed)
I like the pictures in "sample 2" file enclosed
For inspiration, I like design of this brochure: http://www.brelford.ca/HarlowRehab/PatientsFamilies/Clinics_Tests/DKAP_Service/Documents/Brochure.pdf
Here's how I see the pages layout:
----[location: this should be the cover (outside, right panel of trifold)]-----
Vela Mend Logo
Integrated Injury Rehab
Evidence-based, one-on-one care to make your recovery fast and comfortable
www.velamendgroup.ca
---------------[location: inside, left panel]----------------------------------------
Our team leaders
[portrait here]
Harriet Olsavik, MD, FRCPC, MSC, CIME
Physiatrist
Dr. Olsavik specializes in injury rehab and sports medicine. She is highly trained having received her MD and Residency in Physiatry from Pellham Institute. Her passion is to help injured people get back to their life.
[portrait here]
Wendy Carstairs, PT
Physiotherapist
Wendy has over 10 years of experience as a Physiotherapist (5 in Canada). She has advanced training in orthopedics and manual therapy. She loves and relates well with people from the youngest to the most senior.
--------------------[location: inside, middle panel]-------------------------------
Our services
We provide integrated assessment and care from interprofessional team of regulated healthcare professionals with proven experience in injury rehabilitation:
physiatrists
sport medicine physicians
physiotherapists
chiropractors
massage therapists
acupuncturists
psychologists
We provide custom medical bracing, orthotics, orthopedic shoes, assistive devices, and medical stockings, all in one place.
----------------------[location: inside, right panel]-----------------------------------
Only registered physiotherapists
We strongly believe in consistency with your treatment plan. This means that you spend your time here one-on-one with your physiotherapist, not any students or assistants. You get consistent high quality care from a professional.
One-on-one attention
We book maximum 3 people per hour to ensure everyone gets adequate one-on-one time with their physiotherapist. This compares favorably with other clinics, who may book upwards of 5-6 per hour. The atmosphere is professional -balanced with friendly, caring and relaxed. Our highly qualified staff operate this way to help make your recovery faster and more enjoyable.
------------------------[location: outside, left panel]---------------------------------
The right rehab for your clients
Timely access to comprehensive assessment and treatment
Proven track record in injury rehabilitation
Convenient one-stop service
Customized treatment plans
Integrated, co-ordinated care
Evidence-based care applying leading best practices
Access to specialty clinics: Physiatry and Chronic Pain
-------------------------[location: outside, middle panel]--------------------------
Please call us 555-384-2096
for more information on injury rehabilitation
Vela Mend Group
1862 Wexmoor Rd., Unit 9
Scarborough, ON K4T 8B2
[Please include a line art map designed based on "map" file enclosed]
To make a referral for your clients, contact velamendgroup@corvamail.ca or fax: 555-384-2071. Thank you.
www.velamendgroup.ca
------------------------------------------------------------------------------------------------
Target Market(s)
family doctors, ER docs, lawyers, and general public age (20-50)
Industry/Entity Type
Health And Wellness
Requirements
Must have
- san serif font
- blue and green colors
- clean, sophisticated look
Nice to have
- consumer choice award badge either on front or back of trifold
- see above

```html
<!DOCTYPE html>
<html lang="en">
<head>
<meta charset="utf-8">
<title>Vela Mend – Outside Trifold</title>
<link rel="stylesheet" href="https://fonts.googleapis.com/css2?family=Ubuntu:wght@300;400;500;700&display=swap">
<style>
  :root {
    --sky-top: #9fc6ec;
    --sky-bottom: #eef5fc;
    --grass: #5fa83a;
    --skin: #e9c3a8;
    --shirt: #9fc3e6;
    --blue-deep: #2f6fb4;
    --blue-mid: #4583c6;
    --blue-soft: #6d9fd6;
    --ink-blue: #2f6fb2;
    --ink-grey: #5a5a5a;
    --logo-grey: #6b6e72;
    --white: #ffffff;
    --gold: #d6a640;
    --ribbon: #a61e2a;
  }
  * { margin: 0; padding: 0; box-sizing: border-box; }
  html, body { width: 1200px; height: 933px; overflow: hidden; background: var(--white); }
  body { font-family: "Ubuntu", Arial, sans-serif; }
  .flyer { position: relative; width: 1200px; height: 933px; overflow: hidden;
    background: linear-gradient(180deg, var(--sky-top) 0%, var(--sky-bottom) 45%, var(--white) 60%); }
  .photo { position: absolute; }
  .photo-stretch { left: 0; top: 0; width: 500px; height: 560px;
    background: linear-gradient(180deg, #a9cdef 0%, #e4eef8 45%, #f6f8fb 58%, #8cc260 64%, var(--grass) 100%); }
  .photo-knee { left: 735px; top: 0; width: 465px; height: 600px;
    background: linear-gradient(200deg, var(--shirt) 0%, #c8dcee 30%, var(--skin) 55%, #f0d4bf 100%); }
  .award { position: absolute; left: 48px; top: 14px; width: 140px; height: 140px; border-radius: 50%; background: var(--gold); }
  .curve { position: absolute; left: 0; top: 0; }
  .trim { position: absolute; width: 0; height: 16px; border-left: 1px dashed #555; }
  .call { position: absolute; left: 400px; width: 400px; top: 122px; text-align: center; color: var(--ink-blue); }
  .call-lead { font-size: 16px; font-weight: 300; }
  .call-phone { font-size: 34px; font-weight: 500; letter-spacing: 1.5px; margin: 4px 0 2px; }
  .call-sub { font-size: 16px; font-weight: 300; line-height: 21px; }
  .callout { position: absolute; left: 0; top: 418px; width: 285px; height: 94px; background: var(--white);
    border-radius: 0 14px 14px 0; padding: 17px 0 0 65px; color: var(--ink-grey); font-size: 24px; font-weight: 300; line-height: 32px; }
  .benefits { position: absolute; left: 55px; top: 556px; width: 300px; list-style: none; color: var(--white); font-size: 16px; font-weight: 300; line-height: 21px; }
  .benefits li { position: relative; padding-left: 11px; margin-bottom: 12px; }
  .benefits li::before { content: "•"; position: absolute; left: 0; }
  .contact { position: absolute; left: 452px; top: 410px; color: var(--white); font-size: 16px; font-weight: 300; line-height: 22px; }
  .contact-name { font-weight: 500; }
  .map { position: absolute; left: 458px; top: 482px; width: 284px; height: 238px; background: rgba(255,255,255,0.14); }
  .referral { position: absolute; left: 452px; top: 761px; width: 320px; color: var(--white); font-size: 15.5px; font-weight: 300; line-height: 22px; }
  .referral strong { font-weight: 500; letter-spacing: 0.5px; }
  .web { position: absolute; top: 847px; color: var(--white); font-size: 15px; font-weight: 300; letter-spacing: 1.5px; }
  .web b { font-weight: 500; }
  .logo { position: absolute; left: 935px; top: 360px; width: 192px; height: 192px; border-radius: 50%; background: var(--white);
    display: flex; flex-direction: column; align-items: center; justify-content: center; }
  .logo-name { font-size: 30px; font-weight: 700; color: var(--logo-grey); line-height: 34px; }
  .logo-tag { font-size: 10px; font-weight: 400; color: var(--logo-grey); margin-top: 6px; padding-top: 4px; border-top: 3px solid var(--blue-deep); }
  .promise { position: absolute; left: 862px; top: 601px; color: var(--white); font-size: 24px; font-weight: 300; line-height: 32px; }
  .promise b { font-weight: 500; }
  .rule { position: absolute; left: 862px; top: 786px; width: 70px; height: 3px; background: var(--white); }
</style>
</head>
<body>
<main class="flyer">
  <div class="photo photo-stretch" role="img" aria-label="Photo of a young woman in white stretching on green grass under a blue sky"></div>
  <div class="photo photo-knee" role="img" aria-label="Photo of a physiotherapist examining a patient's knee"></div>
  <div class="award" role="img" aria-label="Award badge"></div>

  <svg class="curve" width="1200" height="933" viewBox="0 0 1200 933" aria-hidden="true">
    <defs>
      <linearGradient id="panelBlue" x1="0" y1="0" x2="0" y2="1">
        <stop offset="0" stop-color="var(--blue-deep)"/>
        <stop offset="0.5" stop-color="var(--blue-mid)"/>
        <stop offset="1" stop-color="var(--blue-soft)"/>
      </linearGradient>
    </defs>
    <path d="M0,400 Q600,240 1200,540 L1200,933 L0,933 Z" fill="var(--white)"/>
    <path d="M0,560 L0,425 Q600,280 1200,568 L1200,933 L0,933 Z" fill="url(#panelBlue)"/>
  </svg>

  <span class="trim" style="left:405px;top:0"></span>
  <span class="trim" style="left:797px;top:0"></span>
  <span class="trim" style="left:405px;top:917px"></span>
  <span class="trim" style="left:797px;top:917px"></span>

  <section class="call">
    <p class="call-lead">Please call us</p>
    <p class="call-phone">555-384-2096</p>
    <p class="call-sub">for more information<br>on injury rehabilitation</p>
  </section>

  <h2 class="callout">The right rehab<br>for your clients</h2>
  <ul class="benefits">
    <li>Timely access to comprehensive assessment and treatment</li>
    <li>Proven track record in injury rehabilitation</li>
    <li>Convenient one-stop service</li>
    <li>Customized treatment plans</li>
    <li>Integrated, co-ordinated care</li>
    <li>Evidence-based care applying leading best practices</li>
    <li>Access to specialty clinics: Physiatry and Chronic Pain</li>
  </ul>

  <address class="contact" style="font-style:normal">
    <p class="contact-name">Vela Mend Group</p>
    <p>1862 Wexmoor Rd., Unit 9</p>
    <p>Scarborough, ON K4T 8B2</p>
  </address>
  <div class="map" role="img" aria-label="Line-art street map showing the clinic location"></div>
  <p class="referral">To make a referral for your clients, contact velamendgroup@corvamail.ca or fax: <strong>555-384-2071</strong>. Thank you.</p>
  <p class="web" style="left:452px">www.<b>velamendgroup</b>.ca</p>

  <div class="logo">
    <span class="logo-name">Vela Mend</span>
    <span class="logo-tag">Integrated Injury Rehab</span>
  </div>
  <p class="promise">Evidence-based,<br>one-on-one care<br>to make <b>your recovery</b><br><b>fast</b> and <b>comfortable</b></p>
  <div class="rule"></div>
  <p class="web" style="left:862px">www.<b>velamendgroup</b>.ca</p>
</main>
</body>
</html>
```